Open Harbor book needs a cover design

I need a front and back cover design that demonstrates a strong sense of possibility that trust can be repaired even if things look bleak. Repairing trust is difficult, but this book is full of wisdom, proven strategies, and doctoral research to help people strengthen relationships and improve trust. It can help any group: business, nonprofit, education, service. Showing diversity of groups and people is very important. For the cover title, there should be a play on words: "Open Harbor: Is it? Within Reach" should have the words "is it?" crossed out and the words "It IS! should be replaced there in a striking way. Perhaps in red ink. For publishing purposes, book will be titled Open Harbor: It IS Within Reach! Please see the attachment for an example. The book layout is approximately 260 pages.

A business self-help book, but the target is any person in a group that feels they have lost trust in each other. It can be just a normal person struggling in a volunteer group they are a part of, or a supervisor whose group is not working well together. It can be a leader who just wants their group to be stronger.

Business Management

• Allise - I believe is being used on the interior of the book for the title page and headings

• Show hope and possibility in the midst of difficulty. Must have a play on the words in the title "Open Harbor: Is it? Within Reach" with crossing out "is it?" with "It IS!" (see attached example) Must include the author's name: Marla Quentin, PhD Must include a smaller tagline: "Practical Steps to Move Teams Forward Again"
• Showing diverse people, or hands. Diverse kinds of groups - not just business. A colorful cover. Maybe show the complexity of trust when it is broken...broken pieces of trust that are then picked up and put together when people work together. Could show people (or images of hands) or other ways to show that it's a choice and it is possible to repair broken trust. I'd also like to convey a sense of a group - not just random people. That they have something at stake to work on repairing trust together and this book can help them.
• If images of people are used, just showing one gender or race is not okay. Nor just binary choices: like an image containing one man and one woman, or one white person and one person of color - otherwise it seems that the book on Open Harbor is about race or gender relations.

```html
<!DOCTYPE html>
<html lang="en">
<head>
<meta charset="utf-8">
<title>Open Harbor — Book Cover</title>
<link rel="stylesheet" href="https://fonts.googleapis.com/css2?family=Cinzel:wght@400;500&family=Playfair+Display:wght@700;900&display=swap">
<style>
  :root {
    --stage: #1d1d20;
    --cover-deep: #241660;
    --cover-mid: #3a1f86;
    --cover-violet: #7a3aa8;
    --cover-orchid: #b560c4;
    --cover-pink: #d48ad6;
    --title-white: #ffffff;
    --strike-red: #d42a1e;
    --tagline: #efe3f7;
    --frame: #f4f1f6;
    --office-a: #9fb0bf;
    --office-b: #5d6f86;
    --table-a: #b68a5c;
    --table-b: #6d4d33;
  }
  html, body {
    margin: 0;
    padding: 0;
    width: 1200px;
    height: 905px;
    overflow: hidden;
    background: var(--stage);
  }
  .canvas {
    position: relative;
    width: 1200px;
    height: 905px;
  }
  .book-cover {
    position: absolute;
    left: 326px;
    top: 18px;
    width: 548px;
    height: 868px;
    overflow: hidden;
    background: linear-gradient(160deg, var(--cover-deep) 0%, var(--cover-mid) 55%, var(--cover-violet) 100%);
    box-shadow: 0 12px 40px rgba(0,0,0,0.55);
  }
  .cover-art {
    position: absolute;
    inset: 0;
    width: 548px;
    height: 868px;
  }
  .author-name {
    font-family: "Cinzel", serif;
    font-weight: 400;
  }
  .title-word {
    font-family: "Playfair Display", serif;
    font-weight: 900;
  }
  .tagline {
    font-family: "Cinzel", serif;
    font-weight: 500;
  }
  .publisher-name {
    font-family: "Cinzel", serif;
    font-weight: 500;
  }
</style>
</head>
<body>
<main class="canvas">
  <section class="book-cover" aria-label="Front cover: Open Harbor — It IS Within Reach! by Marla Quentin, PhD">
    <svg class="cover-art" viewBox="0 0 548 868" xmlns="http://www.w3.org/2000/svg">
      <defs>
        <linearGradient id="band-soft" x1="0" y1="1" x2="1" y2="0">
          <stop offset="0" stop-color="#5a2d9c" stop-opacity="0.2"/>
          <stop offset="1" stop-color="#a052c0" stop-opacity="0.75"/>
        </linearGradient>
        <linearGradient id="band-bright" x1="0" y1="1" x2="1" y2="0">
          <stop offset="0" stop-color="#6b36a8"/>
          <stop offset="0.6" stop-color="#b560c4"/>
          <stop offset="1" stop-color="#d48ad6"/>
        </linearGradient>
        <linearGradient id="band-dark" x1="0" y1="0" x2="1" y2="1">
          <stop offset="0" stop-color="#1c1150" stop-opacity="0.9"/>
          <stop offset="1" stop-color="#2e1a74" stop-opacity="0.6"/>
        </linearGradient>
        <linearGradient id="panel-office" x1="0" y1="0" x2="1" y2="1">
          <stop offset="0" stop-color="var(--office-a)"/>
          <stop offset="1" stop-color="var(--office-b)"/>
        </linearGradient>
        <linearGradient id="panel-table" x1="0" y1="0" x2="1" y2="1">
          <stop offset="0" stop-color="var(--table-a)"/>
          <stop offset="1" stop-color="var(--table-b)"/>
        </linearGradient>
      </defs>

      <!-- diagonal colour bands -->
      <g class="background-bands">
        <polygon points="0,300 548,150 548,260 0,430" fill="url(#band-soft)" opacity="0.55"/>
        <polygon points="0,120 548,0 548,60 0,210" fill="url(#band-dark)"/>
        <polygon points="0,560 548,380 548,560 0,700" fill="url(#band-bright)" opacity="0.7"/>
        <polygon points="0,760 548,610 548,868 0,868" fill="url(#band-bright)" opacity="0.85"/>
        <polygon points="0,700 548,560 548,610 0,760" fill="url(#band-dark)" opacity="0.55"/>
      </g>

      <!-- author -->
      <text class="author-name" x="270" y="60" text-anchor="middle" font-size="29" letter-spacing="4" fill="var(--title-white)">MARLA QUENTIN, PHD</text>

      <!-- title -->
      <g class="book-title" fill="var(--title-white)">
        <text class="title-word" x="124" y="237" font-size="180" textLength="285" lengthAdjust="spacingAndGlyphs">OPEN</text>
        <text class="title-word" x="124" y="370" font-size="180" textLength="285" lengthAdjust="spacingAndGlyphs">HARBOR</text>
        <text class="title-word" x="126" y="413" font-size="34" textLength="62" lengthAdjust="spacingAndGlyphs">IT IS</text>
        <text class="title-word" x="126" y="445" font-size="34" textLength="66" lengthAdjust="spacingAndGlyphs">IS IT?</text>
        <text class="title-word" x="196" y="461" font-size="108" textLength="245" lengthAdjust="spacingAndGlyphs">WITHIN REACH</text>
      </g>
      <g class="title-strike" stroke="var(--strike-red)" stroke-width="4" stroke-linecap="round" fill="none">
        <path d="M 110 426 C 140 430, 170 444, 200 452"/>
        <path d="M 112 451 C 140 444, 172 432, 198 424"/>
      </g>

      <!-- photo strip: division to collaboration -->
      <g class="photo-strip">
        <rect x="20" y="491" width="505" height="193" fill="var(--frame)"/>
        <rect x="23" y="494" width="243" height="187" fill="url(#panel-office)" role="img" aria-label="Photo: a tense office meeting, a diverse group of colleagues at odds across a desk"/>
        <rect x="266" y="494" width="256" height="187" fill="url(#panel-table)" role="img" aria-label="Photo: seen from above, a diverse team stacking hands together over a wooden table with laptops"/>
        <line class="strip-divider" x1="272" y1="478" x2="222" y2="700" stroke="var(--frame)" stroke-width="9"/>
      </g>

      <!-- tagline -->
      <g class="tagline" fill="var(--tagline)" font-size="18" letter-spacing="0.5">
        <text x="258" y="722">PRACTICAL STEPS</text>
        <text x="258" y="742">TO MOVE TEAMS</text>
        <text x="258" y="762">FORWARD AGAIN</text>
      </g>

      <!-- publisher -->
      <g class="publisher" fill="var(--title-white)">
        <rect x="208" y="795" width="18" height="18"/>
        <text class="publisher-name" x="232" y="804" font-size="11">KEYSTONE</text>
        <text class="publisher-name" x="232" y="816" font-size="11">PRESS</text>
      </g>
    </svg>
  </section>
</main>
</body>
</html>
```